Advanced Therapeutic Massage Therapist

I need a business card advertising my massage services as an advanced therapeutic massage therapist. I offer advanced therapeutic massage, swedish and deep tissue. I want to create a simple, professional and feminine card. I like bright colours and creativity.

I prefer a bold and experimental approach rather than something status-quo. A card to suggest therapeutic healing through dynamic massage. Motifs, shapes or layout which suggest movement and flow.
Updates

Target Market(s)

Everybody!

Industry/Entity Type

Health And Wellness

Contact Information for Business Card

The card should include:
My name, logo, services offered and my contact details.

Sláine Dunleavy
Massage Therapist

- Swedish - Deep Tissue - Advanced Therapeutic

Phone: (+353) 87 216 4093
Email: regenerate@slainedunleavy-example.com
Website: www.slainedunlevy-example.com

Font styles to use
Serif
Sans Serif
Decorative
Script

Colors

Designer to choose colors to be used in the design.

Requirements
Must have
• An example may contain something like this, yet concise:
• "Sláine Dunleavy
• Massage Therapist
• - Swedish - Deep Tissue - Advanced Therapeutic"
Nice to have
• This sentence is optional:
• Imagery such as a logo or symbol. I have attached a file containing a logo I had produced however the name is incorrect now as it is "Sláine" not "Nelly". It could be edited to change it to Sláine.
• I have sent the file as .psd .jpg. .pdf and .png
• I like when the card conveys energy, movement, pressure points, flow etc.
• I just like the designer to follow their own style and ideas. I like bright colours but must have a lot of a base colour to offset it. I really prefer them to follow their own inspiration. That is my preference.
Should not have
• Pine trees, non-native trees to Britain and Ireland, exotic flowers or animals that are not native to Britain and Ireland.
• I don't like brown as the background colour of the card.
• The cars shouldn't look like a wedding invitation i.e too many floral type designs.

```html
<!DOCTYPE html>
<html lang="en">
<head>
<meta charset="UTF-8">
<title>Sláine Dunleavy – Massage Therapist Business Card</title>
<link rel="stylesheet" href="https://fonts.googleapis.com/css2?family=Quicksand:wght@400;500&family=Work+Sans:wght@400;500&display=swap">
<style>
  :root {
    --page-bg: #e4e4e2;
    --card-white: #ffffff;
    --charcoal: #3b3b3a;
    --gold: #d69a2d;
    --ink: #444444;
    --soft-ink: #777777;
    --mint: #a9d9cc;
    --mint-deep: #7fc2b1;
  }
  * { margin: 0; padding: 0; box-sizing: border-box; }
  html, body {
    width: 1200px;
    height: 900px;
    overflow: hidden;
    background: var(--page-bg);
  }
  .canvas {
    position: relative;
    width: 1200px;
    height: 900px;
  }
  .card {
    position: absolute;
    left: 320px;
    width: 560px;
    height: 320px;
    border-radius: 18px;
    overflow: hidden;
    box-shadow: 0 8px 24px rgba(0,0,0,0.18);
  }
  .card--front { top: 100px; background: var(--card-white); }
  .card--back  { top: 480px; background: var(--charcoal); }

  /* brand lockup */
  .brand {
    position: absolute;
    display: flex;
    flex-direction: column;
    align-items: center;
    text-align: center;
  }
  .brand__disc {
    width: 96px;
    height: 96px;
    border-radius: 50%;
    background: radial-gradient(circle at 45% 40%, var(--mint) 0%, var(--mint-deep) 100%);
  }
  .brand__name {
    margin-top: 10px;
    font-family: 'Quicksand', sans-serif;
    font-weight: 500;
    font-size: 20px;
    letter-spacing: 0.5px;
  }
  .card--front .brand { left: 0; right: 0; top: 44px; }
  .card--front .brand__name { color: var(--ink); }
  .card--back .brand { left: 0; right: 0; top: 70px; }
  .card--back .brand__name { color: #e8e8e8; }

  /* contact */
  .contact {
    position: absolute;
    left: 30px;
    top: 196px;
    font-family: 'Work Sans', sans-serif;
    font-size: 14px;
    color: var(--ink);
    list-style: none;
  }
  .contact__item {
    display: flex;
    align-items: center;
    gap: 9px;
    margin-bottom: 6px;
  }
  .contact__icon { width: 12px; height: 12px; flex: none; }

  /* name block */
  .identity {
    position: absolute;
    right: 30px;
    top: 196px;
    text-align: left;
  }
  .identity__name {
    font-family: 'Quicksand', sans-serif;
    font-weight: 500;
    font-size: 27px;
    color: var(--gold);
    line-height: 1.1;
  }
  .identity__role {
    font-family: 'Work Sans', sans-serif;
    font-size: 13px;
    letter-spacing: 1.5px;
    color: var(--ink);
    text-transform: uppercase;
  }

  /* service band */
  .rule {
    position: absolute;
    left: 0; right: 0;
    top: 256px;
    height: 2px;
    background: var(--gold);
  }
  .services {
    position: absolute;
    left: 0; right: 0;
    top: 262px;
    bottom: 0;
    background: var(--charcoal);
    display: flex;
    align-items: center;
    padding-left: 30px;
    font-family: 'Work Sans', sans-serif;
    font-size: 16px;
    color: #f2f2f2;
    gap: 10px;
  }
  .services__dot {
    width: 7px; height: 7px;
    border-radius: 50%;
    background: var(--gold);
  }

  /* back tagline */
  .tagline {
    position: absolute;
    left: 24px; right: 24px;
    top: 252px;
    font-family: 'Work Sans', sans-serif;
    font-size: 13.5px;
    color: #f0f0f0;
    text-align: center;
    letter-spacing: 0.2px;
  }
</style>
</head>
<body>
<main class="canvas">

  <section class="card card--front" aria-label="Business card front">
    <div class="brand">
      <div class="brand__disc"></div>
      <div class="brand__name">Sláine Dunleavy</div>
    </div>

    <ul class="contact">
      <li class="contact__item">
        <svg class="contact__icon" viewBox="0 0 12 12" aria-hidden="true">
          <path d="M3 1 L5 3.5 L4 5 Q5 7 7 8 L8.5 7 L11 9 L9.5 11 Q5 11 2.5 8 Q0.5 5 1 2.5 Z" fill="none" stroke="#d69a2d" stroke-width="1.1"/>
        </svg>
        <span>(+353) 87 216 4093</span>
      </li>
      <li class="contact__item">
        <svg class="contact__icon" viewBox="0 0 12 12" aria-hidden="true">
          <rect x="1" y="2.5" width="10" height="7" fill="none" stroke="#d69a2d" stroke-width="1.1"/>
          <path d="M1 2.5 L6 6.5 L11 2.5" fill="none" stroke="#d69a2d" stroke-width="1.1"/>
        </svg>
        <span>slainemassage@example.com</span>
      </li>
    </ul>

    <div class="identity">
      <div class="identity__name">Sláine Dunleavy</div>
      <div class="identity__role">Massage Therapist</div>
    </div>

    <div class="rule"></div>
    <div class="services">
      <span>Swedish</span>
      <span class="services__dot"></span>
      <span>Deep Tissue</span>
      <span class="services__dot"></span>
      <span>Advanced Therapeutic</span>
    </div>
  </section>

  <section class="card card--back" aria-label="Business card back">
    <div class="brand">
      <div class="brand__disc"></div>
      <div class="brand__name">Sláine Dunleavy</div>
    </div>
    <p class="tagline">ATMQ qualified specialising in advanced therapeutic and deep tissue massage.</p>
  </section>

</main>
</body>
</html>
```